Food packaging label design

The product name Crisparelle, a thin, crispy, and delicious biscuit/cookie made from simple, all natural ingredients. Its name comes from the fact that it looks and tastes a lot like a biscotti cookie, but thinly sliced and much crispier and more delicious than a biscotti. There are currently two flavors: Pure Pecans, and Hazel Cherry.

I am looking for a fresh, eye catchy design to go on the label for a rice paper stand up pouch (pouch sample attached). Label size are as follows:

4 oz bag - Width X Height
top: 4.5" x 3.5" bottom: 4.5" x 1.5"

12 oz bag
top: 6.5" x 5.5" bottom: 6.5" x 1.5"

I would like for the top portion of the packaging to include:

Crisparelle name
Tag line " a thinner, crispier, and more delicious cousin to the biscotti"
simple and natural ingredients

bottom to include:
net weight
ingredients: wheat flour, eggs, sugar, almonds

Attached is a copy of something I created in powerpoint. you can recreate this using graphic designer software per label specs and improve on it or supprise me with something totally awesome. The key is that it that the colors and design needs to pop or contrast against the white rice paper bag and design needs to be eye catchy, fun and whimsical.

Please refer to link below for best practices for creating artwork for labels to ensure correct format for printing.
http://www.brightmarkprint.example/label-articles/best-practices-designing-custom-labels/

Good luck!
Updates

Target Market(s)

educated, health conscious consumers such as customers who shops at green basket, brewlane, market pauls

Industry/Entity Type

Graphic Designer

Requirements
Should not have
• busy or clutter design

```html
<!DOCTYPE html>
<html lang="en">
<head>
<meta charset="utf-8">
<title>Crisparelle Pouch Labels</title>
<link rel="stylesheet" href="https://fonts.googleapis.com/css2?family=Poppins:wght@600;700&family=Rubik:wght@400;500;700&family=Courgette&display=swap">
<style>
  :root {
    --paper: #ffffff;
    --cream: #f2e9dc;
    --cream-deep: #e8dac6;
    --ink: #2a221d;
    --berry: #8a1f1f;
    --tan: #d7a868;
    --tan-deep: #b9833f;
    --line: #2a221d;
    --upc: #c79a6a;
  }
  * { box-sizing: border-box; margin: 0; padding: 0; }
  html, body { width: 1200px; height: 451px; overflow: hidden; background: var(--paper); }
  body { font-family: "Rubik", sans-serif; color: var(--ink); position: relative; }

  .label { position: absolute; top: 0; width: 296px; height: 451px; background: var(--cream); overflow: hidden; }
  .label--front-hazel { left: 0; }
  .label--back-hazel { left: 303px; }
  .label--front-pecan { left: 604px; }
  .label--back-pecan { left: 904px; }

  .top-garnish { position: absolute; left: 0; top: 0; width: 100%; height: 22px;
    background: linear-gradient(180deg, var(--tan-deep), var(--tan) 60%, var(--cream)); }
  .top-garnish--berry { background: linear-gradient(90deg, var(--tan), var(--berry) 10%, var(--tan) 20%, var(--tan) 40%, var(--berry) 50%, var(--tan) 60%, var(--tan) 80%, var(--berry) 90%, var(--tan)); }

  /* front */
  .brand { position: absolute; left: 0; top: 94px; width: 100%; text-align: center;
    font-family: "Poppins", sans-serif; font-weight: 700; font-size: 38px; letter-spacing: 1px; color: var(--ink); }
  .flavor-row { position: absolute; left: 10px; right: 8px; top: 183px; display: flex; align-items: center; gap: 8px; }
  .flavor { text-align: center; line-height: 1; padding-right: 8px; border-right: 1px solid var(--ink); }
  .flavor__script { font-family: "Courgette", cursive; font-size: 15px; display: block; }
  .flavor__caps { font-family: "Rubik", sans-serif; font-size: 9px; font-weight: 500; letter-spacing: .5px; display: block; margin-top: 1px; }
  .tagline { font-size: 10.2px; font-weight: 500; line-height: 1.35; text-transform: uppercase; }
  .tagline em { font-style: normal; color: var(--berry); }
  .window { position: absolute; left: 0; top: 221px; width: 100%; height: 122px; background: var(--paper); }
  .motto { position: absolute; left: 0; top: 364px; width: 100%; text-align: center; font-family: "Courgette", cursive; font-size: 21px; }
  .ingredients { position: absolute; left: 12px; right: 8px; top: 414px; text-align: center; font-size: 8.6px; text-transform: uppercase; }
  .ingredients b { color: var(--berry); }
  .net-wt { position: absolute; right: 8px; bottom: 4px; font-size: 7.5px; font-weight: 700; }

  /* back */
  .story { position: absolute; left: 8px; top: 28px; width: 153px; font-size: 10px; line-height: 14.2px; }
  .nutrition { position: absolute; left: 163px; top: 32px; width: 124px; height: 250px; background: var(--paper);
    border: 1px solid var(--line); padding: 2px 3px; font-size: 5.6px; line-height: 1.25; }
  .nutrition__title { font-family: "Poppins", sans-serif; font-weight: 700; font-size: 13px; line-height: 1; }
  .nutrition__bar { height: 4px; background: var(--line); margin: 1px 0; }
  .nutrition__row { display: flex; justify-content: space-between; border-top: .5px solid var(--line); padding: .6px 0; }
  .nutrition__row--bold { font-weight: 700; }
  .nutrition__row--indent { padding-left: 6px; }
  .nutrition__small { font-size: 4.6px; line-height: 1.3; border-top: .5px solid var(--line); padding-top: 1px; }
  .nutrition__grid { display: grid; grid-template-columns: 1.6fr 1fr .8fr .8fr; font-size: 4.4px; border-top: .5px solid var(--line); }
  .allergens { position: absolute; left: 163px; width: 126px; top: 302px; text-align: center; font-size: 9px; line-height: 12px; text-transform: uppercase; }
  .allergens b { display: block; font-size: 10px; }
  .maker { position: absolute; left: 6px; width: 150px; top: 346px; text-align: center; font-size: 10.4px; line-height: 13.2px; }
  .maker b { display: block; font-size: 11px; }
  .upc-slot { position: absolute; left: 163px; top: 348px; width: 124px; height: 77px; border: 1px solid var(--upc);
    display: flex; align-items: center; justify-content: center; text-align: center; font-size: 8.5px; line-height: 1.3; color: var(--upc); }
  .orders { position: absolute; left: 8px; top: 419px; font-size: 6.2px; font-weight: 700; text-transform: uppercase; }
  .site { position: absolute; left: 8px; top: 428px; font-size: 15px; font-weight: 700; letter-spacing: .2px; }
</style>
</head>
<body>

<!-- Hazel Cherry front -->
<section class="label label--front-hazel">
  <div class="top-garnish top-garnish--berry" role="img" aria-label="Border of hazelnuts and cherries"></div>
  <h1 class="brand">CRISPARELLE</h1>
  <div class="flavor-row">
    <div class="flavor"><span class="flavor__script">Hazel</span><span class="flavor__caps">CHERRY</span></div>
    <p class="tagline">A thinner, <em>crispier,</em> and more delicious cousin to the biscotti</p>
  </div>
  <div class="window"></div>
  <p class="motto">Simple and Natural</p>
  <p class="ingredients"><b>Ingredients:</b> Wheat flour, eggs, sugar, almonds, cherry</p>
  <p class="net-wt">NET WT. 2 OZ.</p>
</section>

<!-- Hazel Cherry back -->
<section class="label label--back-hazel">
  <div class="top-garnish top-garnish--berry" role="img" aria-label="Border of hazelnuts and cherries"></div>
  <p class="story">Crisparelle is a thin, crispy, and delicious biscuit/cookie made from simple, and all natural harvested ingredients. Hazel flavour is made from just 4 simple ingredients: egg whites, all purpose flour, suger, and almonds. The name Crisparelle comes from its twice cooked process and then thinly sliced to perfection. The Crispy, nutty and delicious flavour resemble the of a biscotti, but without the guilt. In fact, except for naturally healthy fat from almonds. Crisparelle is made without any fat at all. it is an ideal snack for the health conscious snaker. Go ahead. Give it a try... There is a Good Chance you will be hooked!!!</p>
  <div class="nutrition">
    <div class="nutrition__title">Nutrition Facts</div>
    <div><b>Serving Size (1 oz)(28g)</b><br><b>Serving Per Container 2</b></div>
    <div class="nutrition__bar"></div>
    <div class="nutrition__row"><span>Amount per serving</span></div>
    <div class="nutrition__row nutrition__row--bold"><span>Calories 90</span><span>Calories from Fat 25</span></div>
    <div class="nutrition__row"><span></span><span>% Daily Value*</span></div>
    <div class="nutrition__row nutrition__row--bold"><span>Total Fat 3g</span><span>5%</span></div>
    <div class="nutrition__row nutrition__row--indent"><span>Saturated Fat 0g</span><span>0%</span></div>
    <div class="nutrition__row nutrition__row--indent"><span>Trans Fat 0g</span><span></span></div>
    <div class="nutrition__row nutrition__row--bold"><span>Cholesterol 0mg</span><span>0%</span></div>
    <div class="nutrition__row nutrition__row--bold"><span>Sodium 15mg</span><span>1%</span></div>
    <div class="nutrition__row nutrition__row--bold"><span>Total Carbohydrate 14g</span><span>5%</span></div>
    <div class="nutrition__row nutrition__row--indent"><span>Dietary Fiber 1g</span><span>4%</span></div>
    <div class="nutrition__row nutrition__row--indent"><span>Sugars 8g</span><span></span></div>
    <div class="nutrition__row nutrition__row--bold"><span>Proteins 3g</span><span></span></div>
    <div class="nutrition__bar"></div>
    <div class="nutrition__row"><span>Vitamin A 0%</span><span>• Vitamin C 0%</span></div>
    <div class="nutrition__row"><span>Calcium 2%</span><span>• Iron 2%</span></div>
    <div class="nutrition__small">*Percent Daily Values are based on a 2,000 calorie diet. Your daily values may be higher or lower depending on your calorie needs:</div>
    <div class="nutrition__grid">
      <span></span><span>Calories:</span><span>2,000</span><span>2,500</span>
      <span>Total Fat</span><span>Less than</span><span>65g</span><span>80g</span>
      <span>Saturated Fat</span><span>Less than</span><span>20g</span><span>25g</span>
      <span>Cholesterol</span><span>Less than</span><span>300mg</span><span>300mg</span>
      <span>Sodium</span><span>Less than</span><span>2,400mg</span><span>2,400mg</span>
      <span>Total Carbohydrate</span><span></span><span>300g</span><span>375g</span>
      <span>Dietary Fiber</span><span></span><span>25g</span><span>30g</span>
    </div>
    <div class="nutrition__small">Calories per gram:<br>Fat 9 &nbsp;&nbsp; Carbohydrate 4 &nbsp;&nbsp; Protein 4</div>
  </div>
  <p class="allergens"><b>Contains:</b>Egg, wheat, and tree nut</p>
  <p class="maker"><b>Made in the U.S.A</b>Create and Distributed by Good Crumb Pantry, LLC. Maple Falls, Georgia</p>
  <div class="upc-slot">Reserved for<br>UPC Label</div>
  <p class="orders">For orders and inquiries, please visit us at:</p>
  <p class="site">WWW.CRISPARELLE.EXAMPLE</p>
</section>

<!-- Pure Pecans front -->
<section class="label label--front-pecan">
  <div class="top-garnish" role="img" aria-label="Border of scattered pecans"></div>
  <h1 class="brand">CRISPARELLE</h1>
  <div class="flavor-row">
    <div class="flavor"><span class="flavor__caps">PURE</span><span class="flavor__script">Pecans</span></div>
    <p class="tagline">A thinner, <em>crispier,</em> and more delicious cousin to the biscotti</p>
  </div>
  <div class="window"></div>
  <p class="motto">Simple and Natural</p>
  <p class="ingredients"><b>Ingredients:</b> Wheat flour, eggs, sugar, almonds</p>
  <p class="net-wt">NET WT. 2 OZ.</p>
</section>

<!-- Pure Pecans back -->
<section class="label label--back-pecan">
  <div class="top-garnish" role="img" aria-label="Border of scattered pecans"></div>
  <p class="story">Crisparelle is a thin, crispy, and delicious biscuit/cookie made from simple, and all natural harvested ingredients. Pecan flavour is made from just 4 simple ingredients: egg whites, all purpose flour, suger, and almonds. The name Crisparelle comes from its twice cooked process and then thinly sliced to perfection. The Crispy, nutty and delicious flavour resemble the of a biscotti, but without the guilt. In fact, except for naturally healthy fat from almonds. Crisparelle is made without any fat at all. it is an ideal snack for the health conscious snaker. Go ahead. Give it a try... There is a Good Chance you will be hooked!!!</p>
  <div class="nutrition">
    <div class="nutrition__title">Nutrition Facts</div>
    <div><b>Serving Size (1 oz)(28g)</b><br><b>Serving Per Container 2</b></div>
    <div class="nutrition__bar"></div>
    <div class="nutrition__row"><span>Amount per serving</span></div>
    <div class="nutrition__row nutrition__row--bold"><span>Calories 90</span><span>Calories from Fat 25</span></div>
    <div class="nutrition__row"><span></span><span>% Daily Value*</span></div>
    <div class="nutrition__row nutrition__row--bold"><span>Total Fat 2.5g</span><span>5%</span></div>
    <div class="nutrition__row nutrition__row--indent"><span>Saturated Fat 0g</span><span>0%</span></div>
    <div class="nutrition__row nutrition__row--indent"><span>Trans Fat 0g</span><span></span></div>
    <div class="nutrition__row nutrition__row--bold"><span>Cholesterol 0mg</span><span>0%</span></div>
    <div class="nutrition__row nutrition__row--bold"><span>Sodium 15mg</span><span>1%</span></div>
    <div class="nutrition__row nutrition__row--bold"><span>Total Carbohydrate 14g</span><span>5%</span></div>
    <div class="nutrition__row nutrition__row--indent"><span>Dietary Fiber 1g</span><span>4%</span></div>
    <div class="nutrition__row nutrition__row--indent"><span>Sugars 8g</span><span></span></div>
    <div class="nutrition__row nutrition__row--bold"><span>Proteins 3g</span><span></span></div>
    <div class="nutrition__bar"></div>
    <div class="nutrition__row"><span>Vitamin A 0%</span><span>• Vitamin C 0%</span></div>
    <div class="nutrition__row"><span>Calcium 2%</span><span>• Iron 2%</span></div>
    <div class="nutrition__small">*Percent Daily Values are based on a 2,000 calorie diet. Your daily values may be higher or lower depending on your calorie needs:</div>
    <div class="nutrition__grid">
      <span></span><span>Calories:</span><span>2,000</span><span>2,500</span>
      <span>Total Fat</span><span>Less than</span><span>65g</span><span>80g</span>
      <span>Saturated Fat</span><span>Less than</span><span>20g</span><span>25g</span>
      <span>Cholesterol</span><span>Less than</span><span>300mg</span><span>300mg</span>
      <span>Sodium</span><span>Less than</span><span>2,400mg</span><span>2,400mg</span>
      <span>Total Carbohydrate</span><span></span><span>300g</span><span>375g</span>
      <span>Dietary Fiber</span><span></span><span>25g</span><span>30g</span>
    </div>
    <div class="nutrition__small">Calories per gram:<br>Fat 9 &nbsp;&nbsp; Carbohydrate 4 &nbsp;&nbsp; Protein 4</div>
  </div>
  <p class="allergens"><b>Contains:</b>Egg, wheat, and tree nut</p>
  <p class="maker"><b>Made in the U.S.A</b>Create and Distributed by Good Crumb Pantry, LLC. Maple Falls, Georgia</p>
  <div class="upc-slot">Reserved for<br>UPC Label</div>
  <p class="orders">For orders and inquiries, please visit us at:</p>
  <p class="site">WWW.CRISPARELLE.EXAMPLE</p>
</section>

</body>
</html>
```